Builder of high-end, expensive tables and other furniture

Build a website that represents what we do. I want a luxury feel that appeals to those who can afford our products. We build very high end tables and other furniture using trees that have fallen or are standing dead. We never cut living trees. Trees are harvested, milled, and kiln dried. Then that lumber is meticulously turned into fine furniture using the best equipment. Our furniture prices range from $1,000-$20,000.

Trying to figure out how to raise my spend.

```html
<!DOCTYPE html>
<html lang="en">
<head>
<meta charset="utf-8">
<title>Fallen Oak Tables</title>
<link href="https://fonts.googleapis.com/css2?family=Lato:wght@400;700&family=Marcellus+SC&display=swap" rel="stylesheet">
<style>
:root{
  --orange:#e8734d;
  --orange-deep:#d9603a;
  --sky:#5bb8f5;
  --sky-deep:#3ea6ec;
  --ink:#222222;
  --muted:#444444;
  --white:#ffffff;
  --black:#000000;
  --heading-shadow:#1f5f8f;
}
*{margin:0;padding:0;box-sizing:border-box}
html,body{width:1200px;height:4501px;overflow:hidden;background:var(--white)}
body{position:relative;font-family:"Lato",sans-serif;color:var(--ink)}
.abs{position:absolute}

/* header */
.site-header{left:0;top:0;width:1200px;height:131px;background:var(--white)}
.brand{display:flex;align-items:center;gap:10px;font-family:"Lato",sans-serif;font-weight:700;font-size:34px;color:var(--orange)}
.brand-mark{width:20px;height:20px;border-radius:50%;background:var(--orange)}
.site-header .brand{position:absolute;left:95px;top:44px}
.main-nav{position:absolute;left:460px;top:57px;display:flex;gap:40px;font-size:19px;text-transform:uppercase;color:var(--ink)}
.main-nav .active{color:var(--orange)}

/* hero */
.hero{left:0;top:131px;width:1200px;height:591px;background:linear-gradient(180deg,#3a3a3a 0%,#585450 45%,#6d5a48 75%,#8f8a85 100%)}
.hero-title{left:0;top:338px;width:1200px;text-align:center;font-family:"Marcellus SC",serif;font-size:52px;color:var(--orange);text-shadow:2px 2px 0 var(--heading-shadow),0 0 8px rgba(255,255,255,.4)}
.btn{display:flex;align-items:center;justify-content:center;font-size:23px;text-transform:uppercase;border-radius:36px 0 36px 0}
.btn-start{left:480px;top:437px;width:241px;height:63px;background:var(--white);color:var(--orange);box-shadow:4px 4px 0 rgba(0,0,0,.35)}
.edge{left:0;width:1200px;height:30px}

/* about */
.about{left:0;top:722px;width:1200px;height:464px;background:linear-gradient(90deg,#7d6b58 0%,#c6b6a2 35%,#ece7e1 58%,#f6f4f2 100%)}
.section-title{font-family:"Marcellus SC",serif;font-size:33px;color:var(--orange);text-shadow:2px 2px 0 var(--heading-shadow)}
.about-title{left:701px;top:770px}
.about-text{left:701px;top:818px;width:420px;font-size:19.5px;line-height:35px;color:var(--muted)}
.btn-learn{left:701px;top:1086px;width:241px;height:66px;background:var(--sky);color:var(--white);box-shadow:4px 4px 0 rgba(0,0,0,.3)}

/* products */
.centered{left:0;width:1200px;text-align:center}
.products-title{top:1265px}
.product-card{top:1333px;width:288px;height:388px;background:var(--sky);border-radius:12px}
.product-photo{position:absolute;left:11px;top:11px;width:266px;height:300px}
.product-photo::after{content:"";position:absolute;left:50%;bottom:-9px;margin-left:-7px;border:7px solid transparent;border-top-color:var(--white);border-bottom:0}
.product-price{position:absolute;left:0;top:336px;width:100%;text-align:center;font-weight:700;font-size:21px;color:var(--white)}

/* process */
.process-title{top:1808px}
.process-photo{width:419px;height:325px}
.process-label{width:323px;height:77px;background:var(--white);box-shadow:0 3px 8px rgba(0,0,0,.35);display:flex;align-items:center;justify-content:center;font-size:31px;color:var(--orange);text-transform:uppercase}

/* testimonials */
.testimonials{left:0;top:2830px;width:1200px;height:472px;background:radial-gradient(ellipse at 50% 50%,#4a2a16 0%,#2e1a0e 60%,#1a100a 100%)}
.testimonials-title{top:2872px;font-size:31px}
.avatar{left:548px;top:2948px;width:112px;height:112px;border-radius:50%;background:linear-gradient(#d8c6b4,#8d7260);border:4px solid var(--white)}
.stars{left:0;top:3090px;width:1200px;display:flex;justify-content:center;gap:6px}
.review-name{top:3136px;font-size:25px;color:var(--orange);text-transform:uppercase;font-weight:700}
.review-text{left:240px;top:3190px;width:720px;text-align:center;font-size:19.5px;line-height:35px;color:var(--white)}
.slider-arrow{width:30px;height:22px}

/* gallery */
.gallery-title{top:3378px}
.gallery-photo{height:398px}
.round-btn{top:3939px;width:56px;height:56px;border-radius:50%;background:var(--white);box-shadow:0 3px 8px rgba(0,0,0,.3);display:flex;align-items:center;justify-content:center}

/* footer */
.site-footer{left:0;top:4070px;width:1200px;height:431px;background:var(--black);color:var(--white)}
.site-footer .brand{position:absolute;left:0;width:1200px;justify-content:center;top:140px;font-size:34px}
.footer-nav{position:absolute;left:0;top:198px;width:1200px;display:flex;justify-content:center;gap:28px;font-size:19px;text-transform:uppercase}
.footer-nav .sep{color:#bbbbbb}
.social{position:absolute;left:0;top:262px;width:1200px;display:flex;justify-content:center;gap:18px}
.social span{width:38px;height:38px;border-radius:9px;background:var(--orange)}
.footer-rule{position:absolute;left:110px;top:350px;width:980px;height:1px;background:#555555}
.copyright{position:absolute;left:0;top:387px;width:1200px;text-align:center;font-size:15px;text-transform:uppercase}
</style>
</head>
<body>

<header class="abs site-header">
  <div class="brand"><span class="brand-mark"></span>Fallen Oak Tables</div>
  <nav class="main-nav">
    <span class="active">Home</span><span>About Us</span><span>Products</span><span>Testimonials</span><span>Gallery</span>
  </nav>
</header>

<section class="abs hero" role="img" aria-label="Dark modern dining room with wooden table and chairs"></section>
<h1 class="abs hero-title">Welcome to Fallen Oak Tables</h1>
<a class="abs btn btn-start">Get Started</a>
<svg class="abs edge" style="top:700px" viewBox="0 0 1200 30" preserveAspectRatio="none"><polygon fill="#f2efec" points="0,30 0,18 40,10 80,22 130,8 180,20 240,6 300,19 360,9 420,21 480,7 540,18 600,10 660,22 720,8 780,19 840,6 900,20 960,9 1020,21 1080,8 1140,18 1200,10 1200,30"/></svg>

<section class="abs about" role="img" aria-label="Bright dining room with round wooden table and chairs"></section>
<h2 class="abs section-title about-title">About Us</h2>
<p class="abs about-text">Lorem ipsum dolor sit amet, consectetur adipiscing elit, sed do eiusmod tempor incididunt ut labore et dolore magna aliqua. Ut enim ad minim veniam, quis nostrud exercitation ullamco laboris nisi ut aliquip ex ea commodo consequat. Duis aute irure dolor in reprehenderit in voluptate velit esse cillum</p>
<a class="abs btn btn-learn">Learn More</a>

<h2 class="abs centered section-title products-title">Products</h2>
<div class="abs product-card" style="left:129px"><div class="product-photo" role="img" aria-label="Grey lounge chair beside wooden wall" style="background:linear-gradient(135deg,#e9e4dd,#b59a7c 60%,#3d3d3d)"></div><div class="product-price">$3,000</div></div>
<div class="abs product-card" style="left:455px"><div class="product-photo" role="img" aria-label="Nursery with wooden crib and rocking chair" style="background:linear-gradient(135deg,#ece4da,#c9ad8c 60%,#a88460)"></div><div class="product-price">$5,350</div></div>
<div class="abs product-card" style="left:783px"><div class="product-photo" role="img" aria-label="Grey sofa with wooden coffee table" style="background:linear-gradient(135deg,#f4f1ec,#cdbfae 55%,#8e8780)"></div><div class="product-price">$9,080</div></div>

<h2 class="abs centered section-title process-title">Our Process</h2>
<svg class="abs" style="left:0;top:1900px" width="1200" height="500"><g stroke="#d7b23a" stroke-width="2" stroke-dasharray="3 4" fill="none"><line x1="568" y1="210" x2="639" y2="210"/><line x1="475" y1="408" x2="520" y2="471"/><line x1="760" y1="408" x2="715" y2="471"/></g></svg>
<div class="abs process-photo" style="left:150px;top:1934px;background:linear-gradient(135deg,#e9c98a,#c98a3a 50%,#5c6a2a);clip-path:polygon(0 0,100% 7%,100% 100%,0 100%)" role="img" aria-label="Combine harvester unloading grain at sunset"></div>
<div class="abs process-label" style="left:194px;top:2231px">Harvested</div>
<div class="abs process-photo" style="left:639px;top:1934px;background:linear-gradient(135deg,#6b5a4a,#a2714a 50%,#7a4a2a);clip-path:polygon(0 0,100% 10%,100% 100%,0 100%)" role="img" aria-label="Sawmill yard with stacked logs"></div>
<div class="abs process-label" style="left:682px;top:2231px">Milled</div>
<div class="abs process-photo" style="left:421px;top:2371px;background:linear-gradient(135deg,#b8a27c,#8a6c44 50%,#4a3a24);clip-path:polygon(0 0,100% 8%,100% 100%,0 100%)" role="img" aria-label="Stack of split dried wood"></div>
<div class="abs process-label" style="left:465px;top:2668px">Kiln Dried</div>

<section class="abs testimonials" role="img" aria-label="Dark walnut cabinet drawers"></section>
<h2 class="abs centered section-title testimonials-title">Testimonials</h2>
<div class="abs avatar" role="img" aria-label="Customer portrait"></div>
<svg class="abs slider-arrow" style="left:107px;top:3054px" viewBox="0 0 30 22"><polygon fill="var(--orange)" points="0,11 12,0 12,7 30,7 30,15 12,15 12,22"/></svg>
<svg class="abs slider-arrow" style="left:1057px;top:3054px" viewBox="0 0 30 22"><polygon fill="var(--orange)" points="30,11 18,0 18,7 0,7 0,15 18,15 18,22"/></svg>
<div class="abs stars">
  <svg width="20" height="20" viewBox="0 0 20 20"><polygon fill="#f5b800" points="10,0 13,7 20,7 14,12 16,20 10,15 4,20 6,12 0,7 7,7"/></svg>
  <svg width="20" height="20" viewBox="0 0 20 20"><polygon fill="#f5b800" points="10,0 13,7 20,7 14,12 16,20 10,15 4,20 6,12 0,7 7,7"/></svg>
  <svg width="20" height="20" viewBox="0 0 20 20"><polygon fill="#f5b800" points="10,0 13,7 20,7 14,12 16,20 10,15 4,20 6,12 0,7 7,7"/></svg>
  <svg width="20" height="20" viewBox="0 0 20 20"><polygon fill="#f5b800" points="10,0 13,7 20,7 14,12 16,20 10,15 4,20 6,12 0,7 7,7"/></svg>
  <svg width="20" height="20" viewBox="0 0 20 20"><polygon fill="#f5b800" points="10,0 13,7 20,7 14,12 16,20 10,15 4,20 6,12 0,7 7,7"/></svg>
</div>
<div class="abs centered review-name">Lorem Ipsum</div>
<p class="abs review-text">Lorem ipsum dolor sit amet, consectetur adipiscing elit, sed do eiusmod tempor incididunt ut labore et dolore magna aliqua.</p>

<h2 class="abs centered section-title gallery-title">Gallery</h2>
<div class="abs gallery-photo" style="left:65px;top:3487px;width:347px;background:linear-gradient(135deg,#e8e4de,#bda98f 60%,#3a3a3a)" role="img" aria-label="Minimal dining table with black chairs"></div>
<div class="abs gallery-photo" style="left:426px;top:3464px;width:348px;height:432px;background:linear-gradient(180deg,#9cc87a,#6a8f48 50%,#a4703c)" role="img" aria-label="Garden patio with wicker furniture and hanging chair"></div>
<div class="abs gallery-photo" style="left:786px;top:3487px;width:348px;background:linear-gradient(135deg,#d8c7a6,#b98a52 55%,#8c6a44)" role="img" aria-label="Wooden outdoor dining table on a terrace"></div>
<div class="abs round-btn" style="left:522px"><svg width="22" height="16" viewBox="0 0 30 22"><polygon fill="var(--orange)" points="0,11 12,0 12,7 30,7 30,15 12,15 12,22"/></svg></div>
<div class="abs round-btn" style="left:618px"><svg width="22" height="16" viewBox="0 0 30 22"><polygon fill="var(--orange)" points="30,11 18,0 18,7 0,7 0,15 18,15 18,22"/></svg></div>

<svg class="abs edge" style="top:4050px;height:40px" viewBox="0 0 1200 40" preserveAspectRatio="none"><polygon fill="#000" points="0,40 0,20 50,12 100,26 150,10 210,24 270,8 330,22 390,11 450,25 510,9 570,21 630,12 690,26 750,10 810,23 870,8 930,22 990,11 1050,25 1110,10 1160,21 1200,14 1200,40"/></svg>
<footer class="abs site-footer">
  <div class="brand"><span class="brand-mark"></span>Fallen Oak Tables</div>
  <nav class="footer-nav">
    <span>Home</span><span class="sep">|</span><span>About Us</span><span class="sep">|</span><span>Products</span><span class="sep">|</span><span>Testimonials</span><span class="sep">|</span><span>Gallery</span>
  </nav>
  <div class="social"><span aria-label="Social link"></span><span aria-label="Social link"></span><span aria-label="Social link"></span></div>
  <div class="footer-rule"></div>
  <p class="copyright">©2023 Copyrights. Fallen Oak Tables. All rights reserved.</p>
</footer>

</body>
</html>
```